Brightway Haus Inc. Business Card Design

Brightway Haus Inc. is in search of a great clean design for our business cards!

Looking to incorporate our full logo and watermark on side one (however, I am open to having the text and watermark separated within the design.)

On side two, I am looking to have contact information (Name, Position, Phone #, Email, Website (www.thebrightwayhaus.ca). Can have the logo and/or watermark as part of the design if applicable.

Please add tagline "Where Shine Counts" on either side 1 or 2. This tagline can be in a sans serif, serif or cursive font as long as it compliments overall design. Capitalization can be title or sentence case depending on how it fits within the design.

Get creative!! Looking for a clean, crisp, premium design! Looking for a glossy card finish with spot UV features when printed. Cards will also be printed with rounded corners. Standard dimensions (3.5 x 2).

Target Market(s)

B2B - primary clients are business owners or property management corporations. (residential jobs are few and far between)

Industry/Entity Type

Business

Contact Information for Business Card

- clean, crisp design
- double sided
- spot UV accents and glossy finish upon printing
- standard business card size (3.5 x 2) with rounded corners
- please see project description for requirements per side

Font styles to use
Sans Serif

Requirements
Must have
• - adequate bleeds with print ready files
• - cohesive design elements between side 1 & 2
• - spot UV elements (can be on both sides or just one, use your discretion)
• - colour pallet should match the logo file provided
• - incorporate tagline "where shine counts" (this tagline can be in a serif or sans serif font as long as it is complimentary to the overall design.
Nice to have
• - Premium elements with a clean design
Should not have
• - Please omit cartoon or whimsical like designs, think premium.
• - Colours should not stray from the pallet of the provided logo.

```html
<!DOCTYPE html>
<html lang="en">
<head>
<meta charset="utf-8">
<title>Brightway Haus Inc. Business Card</title>
<link href="https://fonts.googleapis.com/css2?family=Roboto:wght@400;500;700&display=swap" rel="stylesheet">
<style>
  :root {
    --teal: #12a0a6;
    --teal-dark: #0d9197;
    --navy: #1c1f45;
    --card-light: #efefef;
    --card-light-edge: #e2e2e2;
    --ink: #222428;
    --backdrop: #e4e4e4;
    --white: #ffffff;
  }
  * { margin: 0; padding: 0; box-sizing: border-box; }
  html, body {
    width: 1200px; height: 576px; overflow: hidden;
    background: var(--backdrop);
    font-family: "Roboto", Arial, sans-serif;
  }
  .canvas { position: relative; width: 1200px; height: 576px; }

  .card {
    position: absolute; top: 139px;
    width: 484px; height: 292px;
    border-radius: 14px; overflow: hidden;
    box-shadow: 0 2px 6px rgba(0,0,0,0.12);
  }

  /* Side one */
  .card-front {
    left: 82px;
    background: linear-gradient(160deg, var(--teal) 0%, var(--teal-dark) 100%);
  }
  .front-wordmark {
    position: absolute; left: 0; right: 0; top: 124px;
    display: flex; align-items: center; justify-content: center; gap: 12px;
  }
  .wordmark-square { width: 30px; height: 30px; background: var(--white); }
  .front-wordmark .wordmark-name {
    font-weight: 700; font-size: 36px; color: var(--white); letter-spacing: -0.5px;
  }

  /* Side two */
  .card-back {
    left: 602px;
    background: linear-gradient(135deg, #f4f4f4 0%, var(--card-light) 50%, var(--card-light-edge) 100%);
  }
  .back-wordmark {
    position: absolute; left: 26px; top: 36px;
    display: flex; align-items: center; gap: 12px;
  }
  .back-wordmark .wordmark-square { width: 34px; height: 34px; background: var(--teal); }
  .back-wordmark .wordmark-name {
    font-weight: 700; font-size: 38px; color: var(--navy); letter-spacing: -0.5px;
  }

  .side-tab {
    position: absolute; left: -12px; top: 128px;
    width: 22px; height: 44px; border-radius: 50%;
    background: var(--teal);
  }
  .person { position: absolute; left: 26px; top: 132px; }
  .person-name { font-weight: 700; font-size: 21px; color: var(--teal); }
  .person-role { margin-top: 7px; font-size: 11.5px; color: var(--ink); }

  .contact-list {
    position: absolute; left: 26px; top: 200px;
    list-style: none; font-size: 13px; color: var(--ink);
  }
  .contact-list li { display: flex; align-items: center; gap: 10px; height: 18px; }
  .contact-list svg { width: 11px; height: 11px; fill: var(--teal); flex: none; }
  .contact-list .accent { color: var(--teal); }

  .address {
    position: absolute; right: 24px; top: 200px;
    text-align: right; font-size: 13px; line-height: 18px; color: var(--ink);
  }

  .base-strip {
    position: absolute; left: 0; bottom: 0;
    width: 300px; height: 10px; background: var(--teal);
  }
  .tagline-band {
    position: absolute; right: 0; bottom: 0;
    width: 202px; height: 29px; background: var(--navy);
    clip-path: polygon(14px 0, 100% 0, 100% 100%, 0 100%);
    display: flex; align-items: center; justify-content: flex-end;
    padding-right: 18px;
    font-size: 12px; letter-spacing: 0.8px; color: var(--white);
  }
</style>
</head>
<body>
<main class="canvas">

  <section class="card card-front" aria-label="Business card, side one">
    <div class="front-wordmark">
      <span class="wordmark-square" aria-hidden="true"></span>
      <span class="wordmark-name">Brightway Haus Inc.</span>
    </div>
  </section>

  <section class="card card-back" aria-label="Business card, side two">
    <div class="back-wordmark">
      <span class="wordmark-square" aria-hidden="true"></span>
      <span class="wordmark-name">Brightway Haus Inc.</span>
    </div>

    <span class="side-tab" aria-hidden="true"></span>

    <div class="person">
      <p class="person-name">Dana Reyes</p>
      <p class="person-role">Managing Director</p>
    </div>

    <ul class="contact-list">
      <li>
        <svg viewBox="0 0 24 24" aria-hidden="true"><path d="M6.6 10.8a15.1 15.1 0 0 0 6.6 6.6l2.2-2.2a1 1 0 0 1 1-.25 11.4 11.4 0 0 0 3.6.57 1 1 0 0 1 1 1V20a1 1 0 0 1-1 1A17 17 0 0 1 3 4a1 1 0 0 1 1-1h3.5a1 1 0 0 1 1 1c0 1.25.2 2.45.57 3.57a1 1 0 0 1-.25 1z"/></svg>
        1800-555-0142
      </li>
      <li>
        <svg viewBox="0 0 24 24" aria-hidden="true"><path d="M2 5h20v14H2z M2 5l10 8 10-8" fill="var(--teal)"/><path d="M3 6l9 7 9-7" fill="none" stroke="#efefef" stroke-width="2"/></svg>
        dana@brightwayhaus.ca
      </li>
      <li>
        <svg viewBox="0 0 24 24" aria-hidden="true"><circle cx="12" cy="12" r="10"/><path d="M2 12h20M12 2c3 3 3 17 0 20M12 2c-3 3-3 17 0 20" fill="none" stroke="#efefef" stroke-width="1.6"/></svg>
        <span>www.<span class="accent">thebrightwayhaus</span>.ca</span>
      </li>
    </ul>

    <address class="address" style="font-style: normal;">
      48, Harbour Lane<br>
      Suite 12, Halifax B3H
    </address>

    <span class="base-strip" aria-hidden="true"></span>
    <p class="tagline-band">Where Shine Counts</p>
  </section>

</main>
</body>
</html>
```